Specialised investor in e-mobility and energy wants business card design

We need a business card design that fits our existing corporate design. <The look and feel must be 'sharp'/'clean', dynamic, communicate momentum, professionalism etc (as one would imagine from a firm in the financial sector). We like the idea of a reverse-side of the card that includes the logo, and the name and contact details on the other. We expect the deliverable to be whatever format might be required to be able to get cards printed directly by a service such as kelmo press. Our website is www.zub.capital

```html
<!DOCTYPE html>
<html lang="en">
<head>
<meta charset="utf-8">
<title>ZUB Capital – Business Card</title>
<link href="https://fonts.googleapis.com/css2?family=Montserrat:wght@400;500;700&display=swap" rel="stylesheet">
<style>
  :root {
    --bg: #2a2a2a;
    --card-white: #ffffff;
    --green-dark: #344f25;
    --green-light: #7cb342;
    --accent-faint: #eceeea;
    --text: #2b2b2b;
    --on-dark: #ffffff;
  }
  * { margin: 0; padding: 0; box-sizing: border-box; }
  html, body { width: 1200px; height: 1059px; overflow: hidden; }
  body {
    background: var(--bg);
    font-family: "Montserrat", sans-serif;
    position: relative;
  }
  .card {
    position: absolute;
    border-radius: 22px;
    overflow: hidden;
  }
  .card--front {
    left: 257px; top: 89px; width: 687px; height: 390px;
    background: var(--card-white);
  }
  .card--back {
    left: 254px; top: 547px; width: 693px; height: 393px;
    background: var(--green-dark);
    display: flex; align-items: center; justify-content: center;
  }
  .front-accent {
    position: absolute; left: 0; top: 0; width: 687px; height: 390px;
  }
  .brand {
    font-weight: 500;
    letter-spacing: 0.5px;
    white-space: nowrap;
  }
  .card--front .brand {
    position: absolute; left: 37px; top: 44px;
    font-size: 49px; color: var(--green-dark);
  }
  .card--back .brand {
    font-size: 84px; color: var(--on-dark);
  }
  .person { position: absolute; left: 38px; top: 152px; }
  .person__name {
    font-weight: 700; font-size: 28px; letter-spacing: 1px;
    color: var(--green-dark); line-height: 1;
  }
  .person__name .surname { color: var(--green-light); }
  .person__role {
    font-size: 16px; color: var(--text); margin-top: 5px; letter-spacing: 0.5px;
  }
  .address {
    position: absolute; left: 38px; top: 220px;
    font-size: 16px; line-height: 22px; color: var(--text); letter-spacing: 0.5px;
  }
  .contacts {
    position: absolute; left: 37px; top: 275px;
    list-style: none; font-size: 16.5px; color: var(--text); letter-spacing: 0.5px;
  }
  .contacts li { display: flex; align-items: center; height: 27px; }
  .contacts svg { width: 13px; height: 13px; margin-right: 7px; fill: var(--green-light); }
</style>
</head>
<body>
  <section class="card card--front" aria-label="Business card front">
    <svg class="front-accent" viewBox="0 0 687 390" aria-hidden="true">
      <circle cx="640" cy="250" r="215" fill="var(--accent-faint)"/>
    </svg>
    <div class="brand">ZUB Capital</div>
    <div class="person">
      <div class="person__name">MARTEN <span class="surname">OLBY</span></div>
      <div class="person__role">Director/Founder</div>
    </div>
    <div class="address">1234 Street Name<br>Country Name AB 5748</div>
    <ul class="contacts">
      <li>
        <svg viewBox="0 0 24 24" aria-hidden="true"><path d="M6.6 10.8a15 15 0 0 0 6.6 6.6l2.2-2.2c.3-.3.7-.4 1-.2 1.1.4 2.3.6 3.6.6.6 0 1 .4 1 1V20c0 .6-.4 1-1 1A17 17 0 0 1 3 4c0-.6.4-1 1-1h3.5c.6 0 1 .4 1 1 0 1.3.2 2.5.6 3.6.1.3 0 .7-.2 1z"/></svg>
        123-555-0184
      </li>
      <li>
        <svg viewBox="0 0 24 24" aria-hidden="true"><path d="M2 5h20v2l-10 7L2 7z"/><path d="M2 9l10 7 10-7v10H2z"/></svg>
        info@zub.capital
      </li>
      <li>
        <svg viewBox="0 0 24 24" aria-hidden="true"><circle cx="12" cy="12" r="10"/></svg>
        &nbsp;www.zub.capital
      </li>
    </ul>
  </section>

  <section class="card card--back" aria-label="Business card back">
    <div class="brand">ZUB Capital</div>
  </section>
</body>
</html>
```